Tarnwell Climate Business Card Design

Design new, 2 sides, business cards for a residential and light commercial heating, air conditioning contractor.

Target Market(s)

Homeowners, small businesses

Industry/Entity Type

Business

Contact Information for Business Card

Dominic Westerhall
Phone - 862-415-2736
Email
Address - PO box 518
Brightwater NJ 07912
Website - www.HarborBreezeLLC.example

Requirements
Must have
• logo, company colors, standard size with no die cut, so I can use nova stamp

```html
<!DOCTYPE html>
<html lang="en">
<head>
<meta charset="utf-8">
<title>Tarnwell Climate Business Card</title>
<link rel="stylesheet" href="https://fonts.googleapis.com/css2?family=Montserrat:wght@400;500;600;700&display=swap">
<style>
  :root {
    --maroon: #9c1c38;
    --maroon-dark: #7d1229;
    --maroon-light: #b8314f;
    --orange: #f0892a;
    --ink: #1b1b1b;
    --text: #2a2a2a;
    --paper: #ffffff;
    --stage: #ece9e4;
    --cream: #f7e6c4;
  }
  * { box-sizing: border-box; margin: 0; padding: 0; }
  html, body { width: 1200px; height: 913px; overflow: hidden; }
  body {
    background: var(--stage);
    font-family: "Montserrat", sans-serif;
    display: flex;
    align-items: center;
    justify-content: center;
    gap: 44px;
  }
  .card {
    position: relative;
    width: 530px;
    height: 303px;
    border-radius: 12px;
    overflow: hidden;
    box-shadow: 0 10px 28px rgba(0,0,0,.18);
  }
  .card-bands { position: absolute; inset: 0; width: 100%; height: 100%; }

  /* front */
  .card--front { background: var(--paper); }
  .brand {
    position: absolute;
    display: flex;
    align-items: center;
    gap: 10px;
    font-weight: 700;
    white-space: nowrap;
  }
  .brand-dot { border-radius: 50%; flex: none; }
  .card--front .brand { left: 34px; top: 112px; font-size: 24px; color: var(--maroon); }
  .card--front .brand-dot { width: 16px; height: 16px; background: var(--orange); }

  .person { position: absolute; right: 36px; top: 36px; text-align: right; }
  .person-name {
    font-size: 22px; font-weight: 600; letter-spacing: 1px;
    color: var(--orange); text-transform: uppercase;
  }
  .person-rule { height: 1px; width: 250px; background: var(--text); margin: 4px 0 3px auto; }
  .person-role { font-size: 12px; color: var(--text); }

  .address {
    position: absolute; right: 36px; top: 108px;
    text-align: right; font-size: 13px; line-height: 1.45; color: var(--text);
    font-style: normal;
  }

  .contact { position: absolute; left: 34px; top: 190px; width: 250px; }
  .contact-rule { height: 1px; background: var(--text); margin-bottom: 8px; }
  .contact-list { list-style: none; font-size: 13.5px; line-height: 1.38; color: var(--text); }
  .contact-list li { display: flex; align-items: center; gap: 10px; white-space: nowrap; }
  .contact-list svg { width: 11px; height: 11px; flex: none; fill: var(--orange); }
  .accent { color: var(--orange); }

  /* back */
  .card--back {
    background: linear-gradient(160deg, var(--maroon-light) 0%, var(--maroon) 45%, var(--maroon-dark) 100%);
  }
  .card--back .brand {
    left: 50%; top: 46%; transform: translate(-50%, -50%);
    font-size: 34px; color: var(--cream);
  }
  .card--back .brand-dot { width: 20px; height: 20px; background: var(--orange); }
  .back-web {
    position: absolute; left: 24px; bottom: 13px;
    font-size: 13px; letter-spacing: .4px; color: var(--paper);
  }
  .back-web .accent { color: var(--maroon-light); }
</style>
</head>
<body>

  <section class="card card--front" aria-label="Business card front">
    <svg class="card-bands" viewBox="0 0 530 303" preserveAspectRatio="none" aria-hidden="true">
      <polygon points="0,290 340,290 352,262 530,262 530,303 0,303" fill="var(--ink)"/>
      <polygon points="352,262 358,248 530,248 530,303 340,303" fill="var(--maroon)"/>
    </svg>

    <div class="brand"><span class="brand-dot"></span>Tarnwell Climate</div>

    <div class="person">
      <p class="person-name">Dominic Westerhall</p>
      <div class="person-rule"></div>
      <p class="person-role">Director</p>
    </div>

    <address class="address">
      PO box 518<br>Brightwater NJ 07912
    </address>

    <div class="contact">
      <div class="contact-rule"></div>
      <ul class="contact-list">
        <li><svg viewBox="0 0 24 24"><path d="M6.6 10.8a15.1 15.1 0 0 0 6.6 6.6l2.2-2.2c.3-.3.7-.4 1-.2 1.1.4 2.3.6 3.6.6.6 0 1 .4 1 1V20c0 .6-.4 1-1 1C10.6 21 3 13.4 3 4c0-.6.4-1 1-1h3.5c.6 0 1 .4 1 1 0 1.3.2 2.5.6 3.6.1.3 0 .7-.2 1z"/></svg>862-415-2736</li>
        <li><svg viewBox="0 0 24 24"><path d="M7 1h10a2 2 0 0 1 2 2v18a2 2 0 0 1-2 2H7a2 2 0 0 1-2-2V3a2 2 0 0 1 2-2zm0 3v14h10V4zm5 15.5a1 1 0 1 0 0 2 1 1 0 0 0 0-2z"/></svg>862-415-2790</li>
        <li><svg viewBox="0 0 24 24"><path d="M2 5h20v14H2zm2 2v.5l8 5 8-5V7zm0 2.8V17h16V9.8l-8 5z"/></svg>info@tarnwellclimate.example</li>
        <li><svg viewBox="0 0 24 24"><path d="M12 2a10 10 0 1 0 0 20 10 10 0 0 0 0-20zm0 2c.9 1.2 1.6 2.6 2 4h-4c.4-1.4 1.1-2.8 2-4zM4.3 14a8 8 0 0 1 0-4h3.4a16 16 0 0 0 0 4zm.9 2h2.9c.3 1.3.8 2.5 1.4 3.6A8 8 0 0 1 5.2 16zM8.1 8H5.2a8 8 0 0 1 4.3-3.6C8.9 5.5 8.4 6.7 8.1 8zM12 20c-.9-1.2-1.6-2.6-2-4h4c-.4 1.4-1.1 2.8-2 4zm2.3-6H9.7a14 14 0 0 1 0-4h4.6a14 14 0 0 1 0 4zm.2 5.6c.6-1.1 1.1-2.3 1.4-3.6h2.9a8 8 0 0 1-4.3 3.6zm1.8-5.6a16 16 0 0 0 0-4h3.4a8 8 0 0 1 0 4zm-.4-6c-.3-1.3-.8-2.5-1.4-3.6A8 8 0 0 1 18.8 8z"/></svg><span>www.<span class="accent">tarnwellclimate</span>.example</span></li>
      </ul>
    </div>
  </section>

  <section class="card card--back" aria-label="Business card back">
    <svg class="card-bands" viewBox="0 0 530 303" preserveAspectRatio="none" aria-hidden="true">
      <polygon points="0,262 268,262 282,290 530,290 530,303 0,303" fill="var(--ink)"/>
      <polygon points="282,290 530,290 530,303 288,303" fill="var(--paper)"/>
    </svg>

    <div class="brand"><span class="brand-dot"></span>Tarnwell Climate</div>

    <p class="back-web">www.<span class="accent">tarnwellclimate</span>.example</p>
  </section>

</body>
</html>
```